Web Design for an Innovative Life Science Marketplace

IMPORTANT:
The software is called CS-Cart. It has capabilities and limitations with design features in the software. There is a certain framework that needs to be followed. It is PHP and Linux. It may require add-ons for your design, so please be specific with what is required. It’s preferred the designer has CS-Cart knowledge/experience.

Key Requirements
1. I’d like the design to include an implemented/recommended CS-Cart theme that is consistent with our branding (see the marketing collateral and logo).
2. I then need the additional design changes to that theme to create the below web pages.
3. All designs should be consistent with our branding. All pictures should either be computer generated (clip art-like) or pictures of happy patients. What is a happy patient? Close up photo of someone healthy, happy, and experiencing/enjoying life. Not someone in a hospital or getting care. Please see examples already on the site.

Please see the attached Web Design details in the word document. That document is important to complete the design.

```html
<!DOCTYPE html>
<html lang="en">
<head>
<meta charset="utf-8">
<title>FLOWLINK-QC – Quality Policy</title>
<link href="https://fonts.googleapis.com/css2?family=Roboto:wght@400;500;700&family=Roboto+Condensed:wght@400;700&display=swap" rel="stylesheet">
<style>
:root{
  --teal:#1f978a;
  --teal-dark:#17806f;
  --green:#8cc43c;
  --ink:#444;
  --muted:#666;
  --dark:#2b2b2b;
  --line:#e6e6e6;
}
*{box-sizing:border-box;margin:0;padding:0}
html,body{width:791px;height:1200px;overflow:hidden;background:#fff}
body{font-family:"Roboto",sans-serif;color:var(--ink)}
.page{position:relative;width:791px;height:1200px;overflow:hidden}
.abs{position:absolute}

/* top bar */
.topbar{top:0;left:0;width:791px;height:19px;border-bottom:1px solid var(--line);font-size:7px;color:#555;text-transform:uppercase}
.topbar .item{position:absolute;top:5px;display:flex;align-items:center;gap:5px}
.topbar svg{width:8px;height:8px;fill:var(--teal)}
.btn-sm{position:absolute;top:2px;height:15px;border-radius:8px;color:#fff;font-size:7px;font-weight:700;display:flex;align-items:center;justify-content:center}
.btn-login{left:587px;width:42px;background:var(--teal)}
.btn-register{left:631px;width:53px;background:var(--green)}

/* header */
.brand{top:33px;left:106px;display:flex;align-items:center;gap:5px}
.brand-mark{width:14px;height:14px;border-radius:50%;background:var(--teal)}
.brand-name{font-family:"Roboto Condensed",sans-serif;font-weight:700;font-size:16px;color:var(--teal)}
.cart{top:30px;left:418px;display:flex;gap:6px}
.cart-icon{width:34px;height:29px;background:var(--green);display:flex;align-items:center;justify-content:center}
.cart-title{font-family:"Roboto Condensed",sans-serif;font-size:11px;color:#555}
.cart-sub{font-size:6.5px;color:#777;display:flex;align-items:center;gap:2px}
.cart-sub b{font-family:"Roboto Condensed",sans-serif;font-size:14px;color:var(--green)}
.search{top:32px;left:556px;width:128px;height:23px;border-radius:12px;background:#f4f4f4;box-shadow:0 1px 2px rgba(0,0,0,.08);font-size:7px;color:#aaa;padding:8px 10px}
.search-btn{position:absolute;right:4px;top:4px;width:15px;height:15px;border-radius:50%;background:var(--green);display:flex;align-items:center;justify-content:center}

/* nav */
.nav{top:70px;left:0;width:791px;height:26px;background:var(--teal);display:flex;padding-left:91px}
.nav a{color:#fff;text-decoration:none;font-family:"Roboto Condensed",sans-serif;font-weight:700;font-size:7.5px;line-height:26px;padding:0 15px;border-right:1px solid rgba(0,0,0,.12)}
.nav a:last-child{border-right:0}

/* hero */
.hero{top:96px;left:0;width:791px;height:154px;background:linear-gradient(90deg,#b8855a 0%,#d6b091 30%,#e2c3a8 50%,#9a5b44 75%,#7e4a3a 100%)}

/* section heading with drop letter */
.dropline{display:flex;align-items:flex-end;justify-content:center;font-family:"Roboto Condensed",sans-serif;font-weight:700;text-transform:uppercase}
.dropline .rule{height:1px;background:#555;margin-bottom:8px}
.policy-title{top:280px;left:0;width:791px}
.policy-title .cap{font-size:64px;line-height:56px;color:var(--green)}
.policy-title .rest{font-size:26px;color:#555;line-height:26px}

/* firm band */
.firm{top:371px;left:0;width:481px;height:159px;background:var(--teal)}
.firm-head{position:absolute;top:22px;left:106px;display:flex;align-items:flex-end;gap:2px;color:#fff;font-family:"Roboto Condensed",sans-serif;font-weight:700}
.firm-head .rule{width:14px;height:1px;background:#fff;margin:0 4px 8px 0}
.firm-head .rule.r{width:52px;margin:0 0 8px 6px}
.firm-head .cap{font-size:46px;line-height:40px}
.firm-head .rest{font-size:16px;line-height:18px}
.firm p{position:absolute;top:77px;left:106px;width:350px;font-size:7.4px;line-height:11px;color:#eef}
.firm-photo{top:371px;left:484px;width:307px;height:159px;background:linear-gradient(135deg,#a48a6a 0%,#e6a45a 45%,#c96a35 70%,#6c5040 100%)}

/* commitment columns */
.col{top:575px;width:266px;text-align:center}
.col-head{display:flex;flex-direction:column;align-items:center;font-family:"Roboto Condensed",sans-serif;font-weight:700;text-transform:uppercase}
.col-head .top{display:flex;align-items:flex-end}
.col-head .cap{font-size:44px;line-height:38px;color:var(--teal)}
.col-head .sm{font-size:14px;color:var(--teal);line-height:16px}
.col-head .big{display:flex;align-items:center;font-size:23px;color:#555;line-height:24px}
.col-head .big .rule{height:1px;background:#555;margin:0 4px}
.col p{margin-top:16px;font-size:7.2px;line-height:11px;color:var(--muted)}
.col p b{color:#333}

/* contact band */
.contact{top:748px;left:0;width:791px;height:97px;background:var(--green)}
.c-item{position:absolute;top:25px;display:flex;align-items:center;gap:8px;color:#fff}
.c-ring{width:46px;height:46px;border:2px solid #fff;border-radius:50%;display:flex;align-items:center;justify-content:center}
.c-main{font-family:"Roboto Condensed",sans-serif;font-weight:700;font-size:12px}
.c-sub{font-family:"Roboto Condensed",sans-serif;font-weight:700;font-size:7px;text-transform:uppercase;margin-top:2px}

/* footer */
.footer{top:845px;left:0;width:791px;height:320px;background:var(--dark)}
.connect{position:absolute;top:28px;left:0;width:791px;display:flex;justify-content:center;align-items:flex-end;font-family:"Roboto Condensed",sans-serif;font-weight:700;text-transform:uppercase;color:#ddd}
.connect .cap{font-size:40px;line-height:34px;color:var(--teal)}
.connect .rest{font-size:16px;line-height:16px}
.social{position:absolute;top:69px;left:355px;display:flex;gap:5px}
.social span{width:24px;height:24px;border:1px solid #bbb;border-radius:2px}
.f-head{position:absolute;top:125px;font-family:"Roboto Condensed",sans-serif;font-weight:700;text-transform:uppercase;color:#fff;display:flex;align-items:flex-end}
.f-head .cap{font-size:40px;line-height:34px;color:var(--teal)}
.f-head .rest{font-size:16px;line-height:16px}
.f-head::after{content:"";position:absolute;left:0;bottom:-6px;width:16px;height:2px;background:#fff}
.news-input{position:absolute;top:178px;left:106px;width:161px;height:29px;border-radius:15px;background:#d9d9d9;font-size:7px;color:#777;padding:11px 15px}
.news-btn{position:absolute;top:210px;left:110px;width:85px;height:21px;border-radius:11px;background:var(--teal);color:#fff;font-family:"Roboto Condensed",sans-serif;font-weight:700;font-size:8px;display:flex;align-items:center;justify-content:center}
.posts{position:absolute;top:176px;left:306px;width:163px}
.post{font-size:8.4px;line-height:11.5px;color:#bbb;padding:0 0 7px;margin-bottom:7px;border-bottom:1px solid #444}
.post:last-child{border:0}
.post a{color:var(--teal);text-decoration:underline}
.map{position:absolute;top:178px;left:499px;width:179px;height:98px;background:linear-gradient(120deg,#e3e2dc 0%,#d9dcd0 55%,#a9c3de 70%,#8fb0d3 100%)}

.bottombar{top:1165px;left:0;width:791px;height:35px;background:var(--teal);color:#fff;font-size:6.5px}
.bottombar nav{position:absolute;top:14px;left:114px;display:flex;gap:21px;text-transform:uppercase}
.bottombar .copy{position:absolute;top:13px;right:106px;text-transform:uppercase}
</style>
</head>
<body>
<div class="page">

  <div class="abs topbar">
    <div class="item" style="left:106px"><svg viewBox="0 0 10 10"><path d="M0 2l3-1 4 1 3-1v7l-3 1-4-1-3 1z"/></svg>Adress : 48 Sample Avenue, NY</div>
    <div class="item" style="left:263px"><svg viewBox="0 0 10 10"><rect x="0" y="2" width="10" height="7"/></svg>Email : info@flowlinkqc.com</div>
    <div class="item" style="left:406px"><svg viewBox="0 0 10 10"><rect x="0" y="0" width="10" height="10" rx="2"/></svg>Call us : 555-014-2290</div>
    <div class="item" style="left:521px"><svg viewBox="0 0 10 10"><circle cx="5" cy="3" r="2.5"/><path d="M0 10c0-4 10-4 10 0z"/></svg>My account</div>
    <div class="btn-sm btn-login">LOGIN</div>
    <div class="btn-sm btn-register">REGISTER</div>
  </div>

  <div class="abs brand"><span class="brand-mark"></span><span class="brand-name">FLOWLINK-QC</span></div>

  <div class="abs cart">
    <div class="cart-icon"><svg width="22" height="18" viewBox="0 0 22 18" fill="none" stroke="#fff" stroke-width="1.6"><path d="M1 2h4l3 10h10l3-7H6"/><circle cx="9" cy="15.5" r="1.5"/><circle cx="17" cy="15.5" r="1.5"/></svg></div>
    <div><div class="cart-title">SHOPPING CART</div><div class="cart-sub"><b>(0)</b>ITEM SELECTED</div></div>
  </div>
  <div class="abs search">Search Product...
    <div class="search-btn"><svg width="8" height="8" viewBox="0 0 10 10" fill="none" stroke="#fff" stroke-width="1.6"><circle cx="4" cy="4" r="3"/><path d="M6.5 6.5L9 9"/></svg></div>
  </div>

  <div class="abs nav">
    <a>HOME</a><a>ABOUT US</a><a>HOW IT WORKS</a><a>OUR PLATFORM</a><a>BENEFITS</a><a>CONTACT US</a>
  </div>

  <div class="abs hero" role="img" aria-label="Close-up photo of a smiling young woman outdoors"></div>

  <div class="abs dropline policy-title">
    <span class="rule" style="width:18px;margin-right:4px"></span><span class="cap">Q</span><span class="rest">uality Policy</span><span class="rule" style="width:52px;margin-left:2px"></span>
  </div>

  <section class="abs firm">
    <div class="firm-head"><span class="rule"></span><span class="cap">O</span><span class="rest">UR QUALITY- DRIVEN FIRM</span><span class="rule r"></span></div>
    <p><b style="color:#fff">FLOWLINK-QC</b> is an innovative firm aspiring to solve waste and procurement problems within the life science supply chain while continuing to maintain the utmost compliance with industry and federal quality standards. Part 11 alignment, vetting of account owners and transactions, and robust GMP information for deals ensure all parties have the information and environment needed to source GMP or non-GMP material.</p>
  </section>
  <div class="abs firm-photo" role="img" aria-label="Photo of a woman with open arms enjoying the sunset"></div>

  <section class="abs col" style="left:106px">
    <div class="col-head">
      <div class="top"><span class="cap">O</span><span class="sm">UR QUALITY</span></div>
      <div class="big"><span class="rule" style="width:18px"></span>COMMITMENT<span class="rule" style="width:50px"></span></div>
    </div>
    <p><b>FLOWLINK-QC</b> is fully committed to the quality of materials and safety of patients. As such, we provide oversight and regulation of the exchange to ensure transactions are transparent, traceable, compliant with the buyer's GMP requirements, and industry aligned.</p>
  </section>
  <section class="abs col" style="left:418px">
    <div class="col-head">
      <div class="top"><span class="cap">O</span><span class="sm">UR QUALITY</span></div>
      <div class="big"><span class="rule" style="width:18px"></span>RESPONSIBILITY<span class="rule" style="width:50px"></span></div>
    </div>
    <p><b>FLOWLINK-QC</b> is fully entrusted and responsible for ensuring access to the exchange is restricted, non-conformance issues are investigated, and parties can seamlessly transact, make payments, and ship products in a professional and private venue for like-minded organizations aspiring to solve life-science waste problems.</p>
  </section>

  <section class="abs contact">
    <div class="c-item" style="left:113px">
      <div class="c-ring"><svg width="20" height="20" viewBox="0 0 24 24" fill="#fff"><path d="M6.6 10.8a15 15 0 006.6 6.6l2.2-2.2a1 1 0 011-.25 11.4 11.4 0 003.6.57 1 1 0 011 1V20a1 1 0 01-1 1A17 17 0 013 4a1 1 0 011-1h3.5a1 1 0 011 1c0 1.25.2 2.45.57 3.57a1 1 0 01-.25 1z"/></svg></div>
      <div><div class="c-main">555-014-2290</div><div class="c-sub">Call us for enquiry</div></div>
    </div>
    <div class="c-item" style="left:308px">
      <div class="c-ring"><svg width="22" height="16" viewBox="0 0 22 16" fill="none" stroke="#fff" stroke-width="1.4"><rect x="1" y="1" width="20" height="14"/><path d="M1 1l10 8 10-8M1 15l7-6M21 15l-7-6"/></svg></div>
      <div><div class="c-main">info@flowlinkqc.com</div><div class="c-sub">Drop us a line anytime!</div></div>
    </div>
    <div class="c-item" style="left:524px">
      <div class="c-ring"><svg width="16" height="22" viewBox="0 0 16 22" fill="#fff"><path d="M8 0a8 8 0 00-8 8c0 6 8 14 8 14s8-8 8-14a8 8 0 00-8-8zm0 11a3 3 0 110-6 3 3 0 010 6z"/></svg></div>
      <div><div class="c-main">48 Sample Avenue, NY</div><div class="c-sub">Company address</div></div>
    </div>
  </section>

  <footer class="abs footer">
    <div class="connect"><span class="cap">C</span><span class="rest">onnect with us</span></div>
    <div class="social"><span></span><span></span><span></span></div>

    <div class="f-head" style="left:106px"><span class="cap">N</span><span class="rest">ewsletter</span></div>
    <div class="f-head" style="left:307px"><span class="cap">T</span><span class="rest">imeline</span></div>
    <div class="f-head" style="left:499px"><span class="cap">L</span><span class="rest">ocation</span></div>

    <div class="news-input">ENTER YOUR EMAIL ID</div>
    <div class="news-btn">SUBSCRIBE</div>

    <div class="posts">
      <div class="post"><a>@flow_qc:</a> Phasellus dapibus tellus at nibh lobortis, vitae placerat sapien tempor.</div>
      <div class="post"><a>@flow_qc:</a> Phasellus dapibus tellus at nibh lobortis, vitae placerat sapien tempor.</div>
      <div class="post"><a>@flow_qc:</a> Phasellus dapibus tellus at nibh lobortis, vitae placerat sapien tempor.</div>
    </div>

    <div class="map" role="img" aria-label="Street map of the company location near the coast"></div>
  </footer>

  <div class="abs bottombar">
    <nav><span>Home</span><span>About us</span><span>How it works</span><span>Our platform</span><span>Benefits</span><span>Contact us</span></nav>
    <div class="copy">© 2018 FLOWLINK . All rights reserved</div>
  </div>

</div>
</body>
</html>
```